Emerging automotive detailing business

I am starting a small automotive detailing business in hopes of becoming a well-known detailer to work on high end cars. I would like a card to reflect the high quality and time I put into my work. The name of the company is Bright Crest Detailing. I feel like it represents racecars getting off the line at the drag strip as well as an innuendo of "Up the Ladder". I do minor paint correction such as clay barring, multi-step buffing and polishing, waxing, hand washes, etc. I am always striving to learn more and improve my work. My goal is to have total customer satisfaction. This is a female run business but I do not want it to be very girly. Elegant is okay! I have pictures of my personal wrenfield attached, they do not need to be incorporated but if you can think of a cool way to use 1 or all of them, go for it!

Target Market(s)

Anyone that owns a vehicle. Preferably high end vehicles such as Valtori, Castellverde and Morvani but I will also happily work on any car, truck or suv no matter what brand.

Industry/Entity Type

Automotive

Contact Information for Business Card

Bright Crest Detailing
Mira Tolland
4175 Quenhollow Rd
Ashmere PA 17492
Cell phone- call/text- 717-555-0148
email- brightcrestdetails@maildrop-example.com
Instagram: @brightcrestdetailing
Facebook: facebook.com/brightcrestdetailing

Requirements
Must have
• Business name, my name, address, phone number. Listing that I do minor paint correction such as clay barring, multi-step buffing and polishing, waxing, hand washes, interior cleaning, and more. (This last part was in nice to haves but I have realized that I do really want it, so I moved it to must haves.) I want something that is different and eye-catching to my customers. Some people have done this very well with cards already submitted to me, but a lot have not. I didn't mess with the "look and feel bars" much because because I am pretty open to the overall design as long as it is not your basic run of the mill design.
Nice to have
• Something car related. Maybe an appointment time/date line. I do not have a logo, but if you would like to design one and incorporate it, that would be amazing!
Should not have
• Purple and Pink colors. Boring, basic, normal card.

```html
<!DOCTYPE html>
<html lang="en">
<head>
<meta charset="utf-8">
<title>Bright Crest Detailing – Business Card</title>
<link rel="stylesheet" href="https://fonts.googleapis.com/css2?family=Open+Sans:wght@400;600;700&display=swap">
<style>
  :root {
    --backdrop: #e9e7e4;
    --card: #ffffff;
    --red: #b5001f;
    --ink: #161616;
    --grey-dark: #4b4b4b;
    --grey-mid: #7b7b7b;
    --grey-light: #cbcbcb;
    --white: #ffffff;
  }
  html, body {
    margin: 0;
    padding: 0;
    width: 1200px;
    height: 1200px;
    overflow: hidden;
    background: var(--backdrop);
    font-family: "Open Sans", Arial, sans-serif;
  }
  .canvas {
    position: relative;
    width: 1200px;
    height: 1200px;
  }
  .card {
    position: absolute;
    top: 188px;
    width: 503px;
    height: 836px;
    background: var(--card);
    box-shadow: 0 6px 18px rgba(0,0,0,0.18);
  }
  .card--front { left: 70px; }
  .card--back  { left: 622px; }
  .card svg { display: block; width: 503px; height: 836px; }
  .brand-name { font-family: "Open Sans", Arial, sans-serif; font-weight: 600; fill: var(--ink); }
  .brand-dot { fill: var(--red); }
  .band-red { fill: var(--red); }
  .band-ink { fill: var(--ink); }
  .band-grey-dark { fill: var(--grey-dark); }
  .band-grey-mid { fill: var(--grey-mid); }
  .band-grey-light { fill: var(--grey-light); }
  .band-text { font-family: "Open Sans", Arial, sans-serif; fill: var(--white); font-weight: 400; }
  .band-title { font-family: "Open Sans", Arial, sans-serif; fill: var(--white); font-weight: 700; }
</style>
</head>
<body>
<main class="canvas">

  <!-- Contact side -->
  <section class="card card--front" aria-label="Contact side">
    <svg viewBox="0 0 503 836" xmlns="http://www.w3.org/2000/svg">
      <g class="brand">
        <circle class="brand-dot" cx="118" cy="175" r="9"/>
        <text class="brand-name" x="136" y="183" font-size="22">Bright Crest Detailing</text>
      </g>

      <g class="chevron">
        <polygon class="band-grey-dark"  points="0,210 465,330 465,345 0,302"/>
        <polygon class="band-grey-mid"   points="0,314 465,352 465,370 0,380"/>
        <polygon class="band-grey-light" points="0,392 465,375 465,395 0,455"/>
      </g>

      <polygon class="band-ink" points="0,455 465,330 465,428 0,552"/>
      <polygon class="band-red" points="0,558 465,434 465,506 0,630"/>
      <polygon class="band-red" points="0,640 465,516 465,590 0,714"/>
      <polygon class="band-red" points="0,722 465,598 465,672 0,796"/>

      <g class="contact">
        <text class="band-text" font-size="24" transform="translate(55,480) rotate(-15)">Mira Tolland 4175 Quenhollow Rd</text>
        <text class="band-text" font-size="24" transform="translate(55,512) rotate(-15)">Ashmere PA 17492</text>
        <text class="band-text" font-size="24" transform="translate(55,590) rotate(-15)">717-555-0148</text>
        <text class="band-text" font-size="24" transform="translate(55,672) rotate(-15)">@brightcrestdetailing</text>
        <text class="band-text" font-size="18" transform="translate(55,754) rotate(-15)">brightcrestdetails@maildrop-example.com</text>
      </g>
    </svg>
  </section>

  <!-- Services side -->
  <section class="card card--back" aria-label="Services side">
    <svg viewBox="0 0 503 836" xmlns="http://www.w3.org/2000/svg">
      <g class="brand">
        <circle class="brand-dot" cx="128" cy="110" r="9"/>
        <text class="brand-name" x="146" y="118" font-size="22">Bright Crest Detailing</text>
      </g>

      <polygon class="band-ink" points="0,268 503,138 503,245 0,372"/>
      <polygon class="band-red" points="0,402 503,272 503,342 0,472"/>
      <polygon class="band-red" points="0,484 503,354 503,424 0,554"/>
      <polygon class="band-red" points="0,566 503,436 503,506 0,636"/>
      <polygon class="band-red" points="0,648 503,518 503,588 0,718"/>
      <polygon class="band-red" points="0,730 503,600 503,670 0,790"/>

      <g text-anchor="middle">
        <text class="band-title" font-size="36" transform="translate(252,268) rotate(-15)">Bright Crest Detailing</text>
        <text class="band-text" font-size="27" transform="translate(252,382) rotate(-15)">Clay Barring</text>
        <text class="band-text" font-size="27" transform="translate(252,464) rotate(-15)">Multi-step Buffing</text>
        <text class="band-text" font-size="27" transform="translate(252,546) rotate(-15)">Polishing</text>
        <text class="band-text" font-size="27" transform="translate(252,628) rotate(-15)">Waxing</text>
        <text class="band-text" font-size="27" transform="translate(252,706) rotate(-15)">Hand washes</text>
      </g>
    </svg>
  </section>

</main>
</body>
</html>
```